Mobile Fitness snd Therapy Business Card Design

I need a business card designed for my mobile fitness and therapy business.

Please view the images that I have uploaded. I like the simplicity of the design that I have attached. I adapted it with my information

Target Market(s)

Those seeking personal training, injury rehabilitation or massage therapy.

Industry/Entity Type

Business

Contact Information for Business Card

Derek Fulham - MSc, CAT(C), RMT, CSCS, Pn2
e-mail: derek@vantrelo.com
website: www.vantrelo.com
instagram: @derek_fulham

Font styles to use
Sans Serif

Colors
3176b5
0355a3

Requirements
Must have
• "Contact us to receive a FREE assessment"
• Services offered:
• Personal Training
• Golf Fitness
• Injury Rehab
• Massage Therapy
• Yoga
Nice to have
• Consistent colours with brand
• - Dark Blue: #232837
• - Blue: #5096f0
• Consistent look/feel with the website: www.vantrelo.com

```html
<!DOCTYPE html>
<html lang="en">
<head>
<meta charset="utf-8">
<title>Vantrelo Business Card</title>
<link href="https://fonts.googleapis.com/css2?family=Roboto:wght@400;500;700&display=swap" rel="stylesheet">
<style>
  :root {
    --navy: #232837;
    --blue: #5096f0;
    --blue-strong: #0355a3;
    --blue-mid: #3176b5;
    --paper: #f4f4f2;
    --ink: #232837;
    --stage: #e6e7ea;
    --white: #ffffff;
  }
  * { box-sizing: border-box; margin: 0; padding: 0; }
  html, body {
    width: 1200px; height: 1000px; overflow: hidden;
    background: var(--stage);
    font-family: "Roboto", Arial, sans-serif;
  }
  .canvas {
    position: relative; width: 1200px; height: 1000px;
  }
  .card {
    position: absolute; left: 250px; width: 700px; height: 400px;
    border-radius: 22px; overflow: hidden;
    box-shadow: 0 10px 30px rgba(20, 25, 40, 0.18);
  }
  /* Back card */
  .card--back {
    top: 60px; background: var(--navy); color: var(--white);
    display: flex; flex-direction: column; align-items: center;
  }
  .brand {
    font-weight: 700; letter-spacing: 10px; line-height: 1;
  }
  .card--back .brand { margin-top: 92px; font-size: 62px; color: var(--white); padding-left: 10px; }
  .tagline {
    font-weight: 500; letter-spacing: 7px; text-transform: uppercase;
  }
  .card--back .tagline { margin-top: 14px; font-size: 20px; color: var(--white); padding-left: 7px; }
  .services-label {
    margin-top: 22px; font-size: 12px; color: var(--blue);
  }
  .services-list {
    margin-top: 6px; font-size: 13px; font-weight: 500; letter-spacing: 0.3px;
    text-transform: uppercase; color: var(--white);
  }
  .offer {
    margin-top: 30px; padding: 6px 12px;
    border: 1.5px solid var(--white); border-radius: 4px;
    font-size: 17px; font-weight: 500;
  }
  .offer strong { color: var(--blue); font-weight: 700; }

  /* Front card */
  .card--front {
    top: 540px; background: var(--paper); color: var(--ink);
  }
  .card--front .brand-block { position: absolute; left: 56px; top: 84px; }
  .card--front .brand { font-size: 46px; color: var(--ink); letter-spacing: 8px; }
  .card--front .tagline { margin-top: 10px; font-size: 14px; letter-spacing: 5px; color: var(--ink); }
  .holder {
    position: absolute; right: 70px; top: 72px; text-align: right;
  }
  .holder-mark {
    position: absolute; right: -70px; top: 0; width: 26px; height: 30px;
    background: var(--blue);
  }
  .holder-name {
    font-size: 22px; font-weight: 700; color: var(--blue-strong);
    text-transform: uppercase; letter-spacing: 0.3px;
  }
  .holder-creds {
    margin-top: 4px; font-size: 13px; font-weight: 500; color: var(--ink);
    text-transform: uppercase;
  }
  .contacts {
    position: absolute; left: 56px; bottom: 52px; list-style: none;
    font-size: 18px; color: var(--ink);
  }
  .contacts li { display: flex; align-items: center; gap: 8px; margin-top: 8px; }
  .contacts svg { width: 17px; height: 17px; flex: none; }
  .contacts .accent { color: var(--blue-strong); font-weight: 700; }
</style>
</head>
<body>
<main class="canvas">

  <section class="card card--back" aria-label="Business card back">
    <div class="brand">VANTRELO</div>
    <div class="tagline">Nutrition - Fitness - Health</div>
    <div class="services-label">Services Offered</div>
    <div class="services-list">Personal Training | Golf Fitness | Injury Rehab | Massage Therapy | Yoga</div>
    <div class="offer">Contact us to receive a <strong>FREE</strong> assessment</div>
  </section>

  <section class="card card--front" aria-label="Business card front">
    <div class="brand-block">
      <div class="brand">VANTRELO</div>
      <div class="tagline">Nutrition - Fitness - Health</div>
    </div>

    <div class="holder">
      <span class="holder-mark"></span>
      <div class="holder-name">Derek Fulham</div>
      <div class="holder-creds">MSc, CAT(C), RMT, CSCS, Pn2</div>
    </div>

    <ul class="contacts">
      <li>
        <svg viewBox="0 0 20 20" aria-hidden="true"><rect x="1" y="4" width="18" height="12" rx="1.5" fill="var(--blue-mid)"/><path d="M2 5l8 6 8-6" fill="none" stroke="#fff" stroke-width="1.6"/></svg>
        <span>derek@vantrelo.com</span>
      </li>
      <li>
        <svg viewBox="0 0 20 20" aria-hidden="true"><circle cx="10" cy="10" r="8" fill="none" stroke="var(--ink)" stroke-width="2"/></svg>
        <span>@derek_fulham</span>
      </li>
      <li>
        <svg viewBox="0 0 20 20" aria-hidden="true"><circle cx="10" cy="10" r="8.5" fill="var(--blue-mid)"/><path d="M1.5 10h17M10 1.5c-3.5 4-3.5 13 0 17M10 1.5c3.5 4 3.5 13 0 17" fill="none" stroke="#fff" stroke-width="1.2"/></svg>
        <span>www.<span class="accent">vantrelo</span>.com</span>
      </li>
    </ul>
  </section>

</main>
</body>
</html>
```